Birchline Septic Solutions

Would like to see some single sided ones but would also like to see some double sided with one sided only being the logo. Owners name is Colin Vandro. Phone number is 555-214-0387
Services are pumping, inspections, installs, and repairs

Contact Information for Business Card

555-241-0387 Colin Vandro Larkmoor Vale

```html
<!DOCTYPE html>
<html lang="en">
<head>
<meta charset="utf-8">
<title>Birchline Septic Solutions – Business Card</title>
<link rel="stylesheet" href="https://fonts.googleapis.com/css2?family=Montserrat:wght@500;600;700;800&display=swap">
<style>
  :root {
    --page-bg: #e9e6e6;
    --card-bg: #f5f2f2;
    --ink: #141414;
    --ink-soft: #2a2a2a;
    --divider: #8a8686;
    --teal: #2dbdbb;
  }
  * { margin: 0; padding: 0; box-sizing: border-box; }
  html, body {
    width: 1200px;
    height: 900px;
    overflow: hidden;
    background: var(--page-bg);
    font-family: "Montserrat", sans-serif;
    color: var(--ink);
  }
  .card {
    position: absolute;
    left: 120px;
    top: 153px;
    width: 960px;
    height: 594px;
    background: var(--card-bg);
    box-shadow: 0 10px 30px rgba(0,0,0,0.12);
  }
  .brand {
    position: absolute;
    left: 0;
    top: 262px;
    width: 522px;
    text-align: center;
    color: var(--ink);
  }
  .brand-name {
    font-size: 62px;
    font-weight: 800;
    line-height: 1;
    letter-spacing: 1px;
  }
  .brand-tagline {
    margin-top: 22px;
    font-size: 20px;
    font-weight: 600;
    letter-spacing: 8px;
    color: var(--ink-soft);
  }
  .divider {
    position: absolute;
    left: 480px;
    top: 168px;
    width: 2px;
    height: 257px;
    background: var(--divider);
  }
  .contact {
    position: absolute;
    left: 520px;
    top: 208px;
  }
  .contact-name {
    font-size: 36px;
    font-weight: 800;
    letter-spacing: 0.5px;
    line-height: 1;
    margin-bottom: 56px;
  }
  .contact-line {
    display: flex;
    align-items: center;
    gap: 14px;
    font-size: 28px;
    font-weight: 500;
    color: var(--ink-soft);
    letter-spacing: 1px;
    height: 44px;
  }
  .contact-line svg { width: 26px; height: 28px; flex: none; }
  .services {
    position: absolute;
    left: 0;
    top: 484px;
    width: 960px;
    height: 58px;
    background: var(--teal);
    display: flex;
    align-items: center;
    justify-content: center;
    gap: 12px;
    font-size: 27px;
    font-weight: 600;
    color: var(--ink);
  }
  .services .dot {
    width: 11px;
    height: 11px;
    border-radius: 50%;
    background: var(--ink);
  }
</style>
</head>
<body>
  <div class="card">
    <div class="brand">
      <div class="brand-name">BIRCHLINE</div>
      <div class="brand-tagline">SEPTIC SOLUTIONS</div>
    </div>

    <div class="divider"></div>

    <div class="contact">
      <div class="contact-name">COLIN VANDRO</div>
      <div class="contact-line">
        <svg viewBox="0 0 24 24" aria-hidden="true">
          <path fill="none" stroke="#141414" stroke-width="2.2" stroke-linejoin="round"
            d="M6.5 3.5l3 3.5-1.8 2.2c1.2 2.6 3.2 4.6 5.8 5.8l2.2-1.8 3.5 3-1.6 3c-7.4-.3-13.3-6.2-13.6-13.6z"/>
          <path fill="none" stroke="#141414" stroke-width="1.8" stroke-linecap="round"
            d="M14 3.5a6.5 6.5 0 0 1 6.5 6.5M14 7a3 3 0 0 1 3 3"/>
        </svg>
        <span>555-214-0387</span>
      </div>
      <div class="contact-line">
        <svg viewBox="0 0 24 28" aria-hidden="true">
          <path fill="#141414" d="M12 1C6.5 1 2.5 5 2.5 10.2 2.5 17 12 27 12 27s9.5-10 9.5-16.8C21.5 5 17.5 1 12 1zm0 13a4 4 0 1 1 0-8 4 4 0 0 1 0 8z"/>
        </svg>
        <span>Larkmoor Vale</span>
      </div>
    </div>

    <div class="services">
      <span>PUMPING</span><span class="dot"></span>
      <span>INSPECTIONS</span><span class="dot"></span>
      <span>INSTALLS</span><span class="dot"></span>
      <span>REPAIRS</span>
    </div>
  </div>
</body>
</html>
```